TK Homes - Stone Dorf Design

Looking for a double sides design, 1 side for my realestate and the other for home building. ( TK Homes on 1 side, Stone Dorf card on the other Side
Side 1 - Marek Tove ~ Vox Realty logo and Company ( the Property quarter )
Marek Tove
Marek@Marektove.example
IG - Marek_Bzq_Realtor
FB - marekt
Cell - 5558130467
3847 61 St Nw

Side 2
Marek Tove
5558130467
IG - Stonedorf_Bzq
Stonedorfdev@mailbox.example

Target Market(s)

Home buyers/ sellers

Industry/Entity Type

Home builders - Realestate

Contact Information for Business Card

Above

Requirements
Must have
• Black OR White background - my information -

```html
<!DOCTYPE html>
<html lang="en">
<head>
<meta charset="utf-8">
<title>TK Homes and Stone Dorf business cards</title>
<link rel="stylesheet" href="https://fonts.googleapis.com/css2?family=Tinos:wght@400;700&display=swap">
<style>
  :root {
    --backdrop: #2b2e33;
    --card: #1e1e21;
    --card-deco: #27272b;
    --blue: #1a6fc0;
    --gold: #f6c537;
    --white: #ffffff;
    --soft-white: #e6e6e6;
  }
  * { box-sizing: border-box; margin: 0; padding: 0; }
  html, body { width: 1200px; height: 780px; overflow: hidden; }
  body {
    background: var(--backdrop);
    font-family: "Tinos", "Times New Roman", serif;
    display: flex;
    align-items: center;
    justify-content: center;
    gap: 40px;
  }
  .card {
    position: relative;
    width: 540px;
    height: 310px;
    background: var(--card);
    border-radius: 22px;
    overflow: hidden;
    box-shadow: 0 14px 34px rgba(0,0,0,.45);
  }
  .deco-name {
    position: absolute;
    right: 40px;
    bottom: -20px;
    font-size: 120px;
    font-weight: 700;
    color: var(--card-deco);
    line-height: 1;
    white-space: nowrap;
  }
  .brand {
    position: absolute;
    display: flex;
    align-items: center;
    gap: 10px;
    font-weight: 700;
    white-space: nowrap;
  }
  .brand-mark { width: 14px; height: 14px; }
  .realty .brand { left: 40px; top: 34px; font-size: 40px; color: var(--blue); }
  .realty .brand-mark { background: var(--gold); }
  .builder .brand { left: 50%; transform: translateX(-50%); top: 36px; font-size: 44px; color: var(--white); letter-spacing: 2px; }
  .builder .brand-mark { background: var(--white); }

  .address { position: absolute; left: 42px; top: 96px; font-size: 17px; color: var(--white); }
  .contacts {
    position: absolute;
    left: 42px;
    list-style: none;
    font-size: 15px;
    color: var(--white);
    line-height: 1.45;
  }
  .realty .contacts { top: 126px; }
  .builder .contacts { top: 118px; }
  .contacts li { display: flex; align-items: center; gap: 8px; }
  .icon { width: 13px; height: 13px; flex: none; }
  .realty .icon { fill: var(--blue); stroke: var(--blue); }
  .builder .icon { fill: var(--white); stroke: var(--white); }
  .dot { width: 11px; height: 11px; border-radius: 50%; flex: none; margin: 0 1px; }
  .realty .dot { background: var(--blue); }
  .builder .dot { background: var(--white); }

  .holder {
    position: absolute;
    right: 52px;
    bottom: 42px;
    text-align: right;
    font-weight: 700;
  }
  .holder-name { font-size: 30px; line-height: 1.05; }
  .holder-role { font-size: 17px; color: var(--white); letter-spacing: 1px; }
  .realty .first { color: var(--blue); }
  .realty .last { color: var(--gold); }
  .builder .holder-name { color: var(--white); }
  .edge-tab {
    position: absolute;
    right: 0;
    bottom: 34px;
    width: 26px;
    height: 54px;
  }
  .realty .edge-tab { background: var(--gold); }
  .builder .edge-tab { background: var(--soft-white); }
</style>
</head>
<body>

<section class="card realty" aria-label="TK Homes real estate side">
  <div class="deco-name" aria-hidden="true">TK Homes</div>
  <div class="brand"><span class="brand-mark"></span>TK Homes</div>
  <p class="address">3847 61 St Nw</p>
  <ul class="contacts">
    <li><svg class="icon" viewBox="0 0 16 16"><path d="M3 1l3 3-2 2c1 2 3 4 5 5l2-2 3 3-2 3C7 15 1 9 1 3z"/></svg>5558130467</li>
    <li><span class="dot"></span>marekt</li>
    <li><span class="dot"></span>Marek_Bzq_Realtor</li>
    <li><svg class="icon" viewBox="0 0 16 16"><rect x="1" y="3" width="14" height="10"/><path d="M1 3l7 6 7-6" fill="none" stroke="#1e1e21" stroke-width="1.5"/></svg>Marek@Marektove.example</li>
    <li><svg class="icon" viewBox="0 0 16 16" fill="none" stroke-width="1.4"><circle cx="8" cy="8" r="6.5" fill="none"/><path d="M1.5 8h13M8 1.5c-3 3-3 10 0 13M8 1.5c3 3 3 10 0 13" fill="none"/></svg>www.marektove.example</li>
  </ul>
  <div class="holder">
    <div class="holder-name"><span class="first">Marek</span> <span class="last">Tove</span></div>
    <div class="holder-role">Director</div>
  </div>
  <div class="edge-tab"></div>
</section>

<section class="card builder" aria-label="Stone Dorf home building side">
  <div class="deco-name" aria-hidden="true">Stone Dorf</div>
  <div class="brand"><span class="brand-mark"></span>Stone Dorf</div>
  <ul class="contacts">
    <li><svg class="icon" viewBox="0 0 16 16"><path d="M3 1l3 3-2 2c1 2 3 4 5 5l2-2 3 3-2 3C7 15 1 9 1 3z"/></svg>5558130467</li>
    <li><span class="dot"></span>Stonedorf_Bzq</li>
    <li><svg class="icon" viewBox="0 0 16 16"><rect x="1" y="3" width="14" height="10"/><path d="M1 3l7 6 7-6" fill="none" stroke="#1e1e21" stroke-width="1.5"/></svg>Stonedorfdev@mailbox.example</li>
  </ul>
  <div class="holder">
    <div class="holder-name">Marek Tove</div>
    <div class="holder-role">Director</div>
  </div>
  <div class="edge-tab"></div>
</section>

</body>
</html>
```